Lumvra App | Pre-Launch Homepage

Dear designer,
Lumvra is a soon to be launched innovative & free social platform for collaborative addictions quitting.
We require a design for our pre-launch homepage that will elevate our basic wireframes to the next level.
We would like the wireframes to serve as a guideline only, and not as a final version of the design. If you have cool ideas - we would appreciate your creativity!
* This is a pre-launch website for a mobile app, and as such the design must be consistent with the general style, design and atmosphere of the app (see screenshot in the shared Drive link).
* We liked the style and feel of the following website: http://tandelhub.example/ - Please let's use it as a reference as well.
* The existing text in the wireframes is there just to represent a place for text. Copy will be edited by us after the design is done.
Please find the wireframes attached, and all relevant design assets and app screenshots in the following Drive shared link -
https://files.example-share.net/open?id=7KQ204RtP3mNxa8Y2Lb61H9cdVzQ
Thanks,
Reginald
Industry/Entity Type
Social
Number of Pages Required
1 page
Look and feel
Each slider illustrates characteristics of the customer's brand and the style your logo design should communicate.

```html
<!DOCTYPE html>
<html lang="en">
<head>
<meta charset="utf-8">
<title>Lumvra App | Pre-Launch Homepage</title>
<link rel="stylesheet" href="https://fonts.googleapis.com/css2?family=Open+Sans:wght@300;400;600;700&family=Roboto:wght@500;700&display=swap">
<style>
:root{
  --yellow:#f5c400;
  --yellow-dark:#d9ab00;
  --ink:#2a2a2c;
  --charcoal:#2e2d30;
  --night:#1f1e22;
  --white:#ffffff;
  --grey-text:#555555;
  --soft-grey:#e4e4e4;
  --muted:#bdbdbd;
}
*{box-sizing:border-box;margin:0;padding:0}
html,body{width:1200px;height:3788px;overflow:hidden}
body{position:relative;font-family:'Open Sans',Arial,sans-serif;color:var(--white);background:var(--white)}
.section{position:absolute;left:0;width:1200px}
.abs{position:absolute}

/* hero */
.hero{top:0;height:540px;background:linear-gradient(180deg,#3b2a1a 0%,#7a4a1c 30%,#c27a2a 48%,#6e4522 66%,#231a14 100%)}
.hero-photo{position:absolute;inset:0;background:radial-gradient(ellipse at 55% 45%,rgba(255,190,90,.55),rgba(0,0,0,0) 55%),linear-gradient(180deg,rgba(0,0,0,.1),rgba(0,0,0,.45))}
.brand{position:absolute;left:0;width:1200px;top:18px;text-align:center;font-family:'Roboto',Arial,sans-serif;font-weight:700;font-size:50px;color:var(--yellow);letter-spacing:1px}
.tagline{position:absolute;left:0;width:1200px;top:84px;text-align:center;font-size:17px;font-weight:600;color:var(--yellow)}
.contact-phone{position:absolute;left:808px;top:18px;display:flex;align-items:center;gap:10px;font-size:13px;color:var(--white)}
.contact-phone .dot{width:26px;height:26px;border-radius:50%;background:rgba(0,0,0,.55);display:flex;align-items:center;justify-content:center}
.menu-btn{position:absolute;left:1040px;top:0;width:70px;height:46px;background:var(--yellow);display:flex;flex-direction:column;align-items:center;justify-content:center;gap:4px}
.menu-btn span{display:block;width:20px;height:3px;background:var(--ink)}
.hero-title{position:absolute;left:40px;top:268px;width:620px;font-family:'Roboto',Arial,sans-serif;font-weight:700;font-size:22px;line-height:30px;text-transform:uppercase}
.btn-yellow{display:inline-block;background:var(--yellow);color:var(--ink);font-weight:600;font-size:14px;text-align:center}
.hero-btn{position:absolute;left:104px;top:384px;width:116px;height:34px;line-height:34px}
.slide-arrow{position:absolute;top:290px;width:30px;height:40px}
.scroll-dots{position:absolute;top:510px;left:548px;display:flex;gap:10px}
.scroll-dots span{width:40px;height:40px;border-radius:50%;background:var(--white);border:3px solid #444;color:#444;font-weight:700;text-align:center;line-height:32px;font-size:20px}

/* phone mockup */
.phone{position:absolute;background:var(--white);border-radius:24px;border:2px solid #d8d8d8;box-shadow:0 6px 18px rgba(0,0,0,.25)}
.phone .screen{position:absolute;left:8%;right:8%;top:14%;bottom:14%;background:linear-gradient(180deg,#3a3530,#1e1c1b)}
.phone .speaker{position:absolute;top:6%;left:38%;width:24%;height:4px;border-radius:2px;background:#c8c8c8}
.phone .home{position:absolute;bottom:3.5%;left:50%;width:34px;height:34px;margin-left:-17px;border-radius:50%;border:2px solid #cfcfcf}

/* features */
.features{top:520px;height:520px;background:linear-gradient(180deg,#2c2b2f,#232226);clip-path:polygon(0 6%,100% 0,100% 100%,0 100%)}
.feature{position:absolute;top:130px;width:260px;text-align:center}
.feature .ring{width:104px;height:104px;margin:0 auto;border-radius:50%;border:4px solid var(--white);display:flex;align-items:center;justify-content:center}
.feature.active .ring{border-color:var(--yellow)}
.feature h3{margin-top:18px;font-size:16px;font-weight:400}
.feature.active h3{color:var(--yellow)}
.feature p{margin-top:8px;font-size:13px;line-height:18px;color:var(--muted)}

/* fun */
.fun{top:1020px;height:520px;background:linear-gradient(100deg,#3c2818 0%,#5a3c22 40%,#2a221d 100%);clip-path:polygon(0 0,100% 6%,100% 100%,0 100%)}
.section-title{font-weight:300;font-size:52px}
.fun .section-title{position:absolute;left:430px;top:70px}
.fun .copy{position:absolute;left:430px;top:160px;width:560px;font-size:15px;line-height:23px}
.fun .copy p+p{margin-top:18px}

/* inspire */
.inspire{top:1500px;height:520px;background:var(--white);clip-path:polygon(0 7%,100% 0,100% 100%,0 92%);color:var(--ink)}
.inspire .section-title{position:absolute;left:560px;top:90px;color:var(--ink)}
.inspire .copy{position:absolute;left:250px;top:180px;width:560px;font-size:15px;line-height:23px;color:var(--grey-text);text-align:center}
.inspire .copy p+p{margin-top:18px}

/* achieve */
.achieve{top:1960px;height:720px;background:linear-gradient(180deg,#2a2a2e,#1c1c20);clip-path:polygon(0 0,100% 8%,100% 92%,0 100%)}
.achieve .section-title{position:absolute;left:0;width:1200px;text-align:center;top:70px}
.achieve .lead{position:absolute;left:330px;width:540px;top:150px;text-align:center;font-size:15px;line-height:22px}
.point{position:absolute;display:flex;align-items:center;gap:18px;width:300px;font-size:12px;line-height:17px;color:var(--muted)}
.point .icon{flex:none;width:46px;height:46px;border-radius:50%;border:2px solid var(--yellow);display:flex;align-items:center;justify-content:center}
.point.right{flex-direction:row-reverse}

/* coming soon */
.coming{top:2640px;height:800px;background:var(--white);color:var(--ink)}
.coming .section-title{position:absolute;left:0;width:1200px;text-align:center;top:40px;color:var(--ink)}
.carousel-arrow{position:absolute;top:270px;width:60px;height:60px;border-radius:50%;border:3px solid var(--yellow);display:flex;align-items:center;justify-content:center}
.stores{position:absolute;top:436px;left:0;width:1200px;display:flex;justify-content:center;gap:50px}
.stores span{width:60px;height:60px;border-radius:10px;background:#3a3a3a}
.subscribe{position:absolute;left:336px;top:540px;width:528px;height:100px;background:var(--soft-grey);padding:18px 30px;text-align:center}
.subscribe h4{font-size:15px;font-weight:600;color:var(--grey-text)}
.subscribe .row{margin-top:14px;display:flex;gap:14px;justify-content:center}
.subscribe .field{width:300px;height:32px;background:var(--white);border:1px solid #cfcfcf;text-align:left;padding-left:10px;font-size:12px;line-height:30px;color:#999}
.subscribe .btn-yellow{width:140px;height:32px;line-height:32px;font-size:13px}

/* footer */
.footer{top:3400px;height:388px;background:linear-gradient(180deg,#2a2824,#1c1b1e);clip-path:polygon(0 8%,100% 0,100% 100%,0 100%)}
.footer .section-title{position:absolute;left:0;width:1200px;text-align:center;top:70px}
.to-top{position:absolute;left:1024px;top:80px;width:40px;height:40px;border-radius:50%;background:var(--white);display:flex;align-items:center;justify-content:center}
.socials{position:absolute;top:170px;left:0;width:1200px;display:flex;justify-content:center;gap:20px}
.socials span{width:62px;height:62px;background:var(--yellow);border-radius:4px}
.socials-band{position:absolute;top:158px;left:420px;width:360px;height:86px;background:rgba(245,196,0,.9)}
.legal{position:absolute;top:272px;left:0;width:1200px;text-align:center;font-size:12px;color:var(--muted)}
.links{position:absolute;top:296px;left:0;width:1200px;text-align:center;font-size:12px;color:var(--muted)}
</style>
</head>
<body>

<!-- Hero -->
<header class="section hero">
  <div class="hero-photo" role="img" aria-label="Sunset photo of children jumping joyfully in silhouette"></div>
  <div class="brand">Lumvra</div>
  <div class="tagline">Become a better version of yourself</div>
  <div class="contact-phone">
    <span class="dot"><svg width="14" height="14" viewBox="0 0 24 24"><path fill="#f5c400" d="M6.6 10.8a15 15 0 0 0 6.6 6.6l2.2-2.2c.3-.3.7-.4 1-.2 1.1.4 2.3.6 3.6.6.6 0 1 .4 1 1V20c0 .6-.4 1-1 1A17 17 0 0 1 3 4c0-.6.4-1 1-1h3.5c.6 0 1 .4 1 1 0 1.3.2 2.5.6 3.6.1.3 0 .7-.2 1z"/></svg></span>
    +1-555-0142
  </div>
  <div class="menu-btn"><span></span><span></span><span></span></div>
  <svg class="slide-arrow" style="left:14px" viewBox="0 0 30 40"><polyline points="22,6 8,20 22,34" fill="none" stroke="#fff" stroke-width="4"/></svg>
  <svg class="slide-arrow" style="left:1156px" viewBox="0 0 30 40"><polyline points="8,6 22,20 8,34" fill="none" stroke="#fff" stroke-width="4"/></svg>
  <h1 class="hero-title">Lumvra is a revolutionary &amp; free social platform for collaborative addictions quitting.</h1>
  <a class="btn-yellow hero-btn">Subscribe</a>
  <div class="phone" style="left:808px;top:196px;width:150px;height:310px">
    <span class="speaker"></span>
    <div class="screen" role="img" aria-label="App screen showing a user profile with avatar and progress stats"></div>
    <span class="home"></span>
  </div>
  <div class="scroll-dots"><span>+</span><span>+</span></div>
</header>

<!-- Features -->
<section class="section features">
  <div class="feature" style="left:150px">
    <div class="ring"><svg width="50" height="50" viewBox="0 0 50 50"><circle cx="25" cy="25" r="19" fill="none" stroke="#fff" stroke-width="9"/><circle cx="25" cy="25" r="19" fill="none" stroke="#e0392b" stroke-width="9" stroke-dasharray="15 15"/></svg></div>
    <h3>Never be alone</h3>
    <p>Forget what you know - Lumvra<br>makes it fun to quit.</p>
  </div>
  <div class="feature active" style="left:470px">
    <div class="ring"><svg width="50" height="50" viewBox="0 0 50 50"><polygon points="25,4 31,19 47,19 34,29 39,45 25,35 11,45 16,29 3,19 19,19" fill="#f5c400"/></svg></div>
    <h3>Network Power</h3>
    <p>Forget what you know - Lumvra<br>makes it fun to quit.</p>
  </div>
  <div class="feature" style="left:790px">
    <div class="ring"><svg width="50" height="50" viewBox="0 0 50 50"><circle cx="25" cy="25" r="18" fill="none" stroke="#fff" stroke-width="3"/><path d="M17 30l8-14 8 14z" fill="#fff"/></svg></div>
    <h3>Stay Motivated</h3>
    <p>Forget what you know - Lumvra<br>makes it fun to quit.</p>
  </div>
</section>

<!-- Fun -->
<section class="section fun">
  <div class="phone" style="left:180px;top:70px;width:160px;height:330px">
    <span class="speaker"></span>
    <div class="screen" style="background:var(--yellow)" role="img" aria-label="App screen illustration of a figure fighting a cravings character"></div>
    <span class="home"></span>
  </div>
  <h2 class="section-title">Fun</h2>
  <div class="copy">
    <p>Forget what you know - Lumvra makes it fun to quit. The battle between your good and bad demons comes to life in our gamified approach for managing your campaigns.</p>
    <p>Lumvra gives you the opportunity to take an active role in helping your network to smash your common addictions as a team. That's right, we converted the cessation process into a social game.</p>
  </div>
</section>

<!-- Inspire -->
<section class="section inspire">
  <h2 class="section-title">Inspire</h2>
  <div class="copy">
    <p>One of the most important factors for successful quitting is the ability to stay inspired during the process.</p>
    <p>That's why we designed Lumvra as a platform where you can inspire and be inspired by a supportive network of awesome Lumvra ninjas!</p>
  </div>
  <div class="phone" style="left:850px;top:60px;width:160px;height:330px">
    <span class="speaker"></span>
    <div class="screen" role="img" aria-label="App screen with a yellow head and lightbulb idea illustration"></div>
    <span class="home"></span>
  </div>
</section>

<!-- Achieve -->
<section class="section achieve">
  <h2 class="section-title">Achieve</h2>
  <p class="lead">Lumvra is built as a pyramid of relationships that makes use of the Social Cognitive Theory, to provide a powerful network of positive reinforcement. The bigger you make it, the stronger you get.</p>
  <div class="phone" style="left:520px;top:250px;width:160px;height:330px">
    <span class="speaker"></span>
    <div class="screen" style="background:var(--yellow)" role="img" aria-label="App screen illustration of three figures on a winners podium"></div>
    <span class="home"></span>
  </div>
  <div class="point" style="left:180px;top:310px">
    <span class="icon"><svg width="22" height="22" viewBox="0 0 24 24"><circle cx="12" cy="5" r="3" fill="#fff"/><path d="M5 12h14M12 9v6l-4 7M12 15l4 7" stroke="#fff" stroke-width="2" fill="none"/></svg></span>
    <span>Lumvra is built as a pyramid of relationships that makes use of the Social</span>
  </div>
  <div class="point" style="left:180px;top:430px">
    <span class="icon"><svg width="22" height="22" viewBox="0 0 24 24"><path d="M12 3v18M3 12h18" stroke="#fff" stroke-width="2"/></svg></span>
    <span>Lumvra is built as a pyramid of relationships that makes use of the Social</span>
  </div>
  <div class="point right" style="left:720px;top:310px">
    <span class="icon"><svg width="22" height="22" viewBox="0 0 24 24"><polygon points="12,3 15,10 22,10 16,14 18,21 12,17 6,21 8,14 2,10 9,10" fill="none" stroke="#fff" stroke-width="2"/></svg></span>
    <span>Lumvra is built as a pyramid of relationships that makes use of the Social</span>
  </div>
  <div class="point right" style="left:720px;top:430px">
    <span class="icon"><svg width="22" height="22" viewBox="0 0 24 24"><circle cx="12" cy="9" r="5" fill="none" stroke="#fff" stroke-width="2"/><path d="M9 14l-2 7 5-3 5 3-2-7" fill="none" stroke="#fff" stroke-width="2"/></svg></span>
    <span>Lumvra is built as a pyramid of relationships that makes use of the Social</span>
  </div>
</section>

<!-- Coming soon -->
<section class="section coming">
  <h2 class="section-title">Coming Soon</h2>
  <div class="phone" style="left:510px;top:128px;width:180px;height:290px">
    <span class="speaker"></span>
    <div class="screen" role="img" aria-label="App screen showing a user profile and daily progress"></div>
    <span class="home"></span>
  </div>
  <div class="carousel-arrow" style="left:200px"><svg width="20" height="20" viewBox="0 0 20 20"><polyline points="13,3 6,10 13,17" fill="none" stroke="#2a2a2c" stroke-width="3"/></svg></div>
  <div class="carousel-arrow" style="left:940px"><svg width="20" height="20" viewBox="0 0 20 20"><polyline points="7,3 14,10 7,17" fill="none" stroke="#2a2a2c" stroke-width="3"/></svg></div>
  <div class="stores"><span></span><span></span><span></span></div>
  <div class="subscribe">
    <h4>Subscribe Below for beta release and updates</h4>
    <div class="row">
      <div class="field">Enter your email address</div>
      <a class="btn-yellow">Let Me Know</a>
    </div>
  </div>
</section>

<!-- Footer -->
<footer class="section footer">
  <h2 class="section-title">Join the revolution</h2>
  <div class="to-top"><svg width="16" height="16" viewBox="0 0 16 16"><polygon points="4,2 13,8 4,14" fill="#2a2a2c"/></svg></div>
  <div class="socials-band"></div>
  <div class="socials"><span style="background:#2a2824"></span><span style="background:#2a2824"></span><span style="background:#2a2824"></span></div>
  <p class="legal">© 2015 Lumvra. All Rights Reserved.</p>
  <p class="links">Contact Us &nbsp;|&nbsp; Terms &nbsp;|&nbsp; Privacy Policy</p>
</footer>

</body>
</html>
```